Single-sided business card for restaurant velmora with new logo made on this site

Business card options with new logo including restaurant name, address, phone number and website. This business card is single-sided only and will be presented at the hostess desk for clients to take. I would like to see options based on a cream card background, a white card background, a yellow card background and a burgundy colored background. It needs to be elegant and traditional.

Target Market(s)

local and international crowd

Industry/Entity Type

restaurant

Contact Information for Business Card

address, website and phone number

Font styles to use
Serif

Colors
EE7325
F08F49
F5BC92
FAE3D3
FDF4ED

Requirements
Must have
• new logo, address, phone number, website
Should not have
• more than three colors

```html
<!DOCTYPE html>
<html lang="es">
<head>
<meta charset="utf-8">
<title>Velmora – Tarjetas de presentación</title>
<link href="https://fonts.googleapis.com/css2?family=Crimson+Text:wght@400;600&display=swap" rel="stylesheet">
<style>
  :root {
    --stage: #2e2e2e;
    --gold: #e8ac35;
    --burgundy: #3b1a18;
    --paper: #f7f7f6;
    --paper-shade: #e6e6e6;
    --text: #4a4a4a;
  }
  html, body {
    margin: 0;
    width: 1200px;
    height: 900px;
    overflow: hidden;
    background: var(--stage);
    font-family: "Crimson Text", Georgia, serif;
  }
  .canvas {
    position: relative;
    width: 1200px;
    height: 900px;
  }
  .card {
    position: absolute;
    width: 700px;
    height: 400px;
    box-sizing: border-box;
    padding: 22px;
    box-shadow: 0 18px 40px rgba(0,0,0,0.45);
  }
  .card--front { left: 90px; top: 40px; background: var(--gold); }
  .card--back { left: 410px; top: 470px; background: var(--burgundy); }
  .card__face {
    position: relative;
    width: 100%;
    height: 100%;
    background: linear-gradient(135deg, #ececec 0%, var(--paper) 45%, #ffffff 100%);
    overflow: hidden;
  }
  .leaf-decoration {
    position: absolute;
    right: 0;
    top: 0;
    width: 52%;
    height: 100%;
    background: radial-gradient(ellipse at 80% 45%, var(--paper-shade) 0%, rgba(230,230,230,0.5) 45%, rgba(247,247,246,0) 75%);
  }
  .brand {
    position: absolute;
    top: 50%;
    display: flex;
    flex-direction: column;
    align-items: center;
    gap: 14px;
    transform: translate(-50%, -50%);
  }
  .card--front .brand { left: 50%; }
  .card--back .brand { left: 175px; }
  .brand__mark {
    width: 120px;
    height: 120px;
  }
  .card--front .brand__mark { background: var(--burgundy); }
  .card--back .brand__mark { background: var(--gold); }
  .brand__name {
    font-size: 44px;
    line-height: 1;
    font-weight: 400;
    letter-spacing: 0.16em;
    text-transform: uppercase;
    color: var(--burgundy);
    white-space: nowrap;
  }
  .contact {
    position: absolute;
    left: 360px;
    top: 50%;
    transform: translateY(-50%);
    list-style: none;
    margin: 0;
    padding: 0;
    color: var(--text);
    font-size: 17px;
    line-height: 1.25;
    white-space: nowrap;
  }
  .contact__item {
    display: flex;
    align-items: flex-start;
    gap: 9px;
    margin-bottom: 8px;
  }
  .contact__icon { width: 15px; height: 15px; flex: none; margin-top: 3px; fill: var(--gold); }
</style>
</head>
<body>
<main class="canvas">
  <section class="card card--front" aria-label="Anverso de la tarjeta">
    <div class="card__face">
      <div class="leaf-decoration" role="img" aria-label="Ilustración tenue de hojas de agave"></div>
      <div class="brand">
        <span class="brand__mark"></span>
        <span class="brand__name">Velmora</span>
      </div>
    </div>
  </section>

  <section class="card card--back" aria-label="Tarjeta con datos de contacto">
    <div class="card__face">
      <div class="leaf-decoration" role="img" aria-label="Ilustración tenue de hojas de agave"></div>
      <div class="brand">
        <span class="brand__mark"></span>
        <span class="brand__name">Velmora</span>
      </div>
      <ul class="contact">
        <li class="contact__item">
          <svg class="contact__icon" viewBox="0 0 16 16" aria-hidden="true"><path d="M3.5 1.5l2.5 0 1 3.5-1.7 1.2a8 8 0 0 0 4.5 4.5L11 9l3.5 1v2.5c0 1-1 2-2 2A11 11 0 0 1 1.5 3.5c0-1 1-2 2-2z"/></svg>
          <span>555-014-2870</span>
        </li>
        <li class="contact__item">
          <svg class="contact__icon" viewBox="0 0 16 16" aria-hidden="true"><circle cx="8" cy="8" r="7"/><path d="M1 8h14M8 1c3 3 3 11 0 14M8 1c-3 3-3 11 0 14" stroke="#fff" stroke-width="1" fill="none"/></svg>
          <span>www.velmora.com.mx</span>
        </li>
        <li class="contact__item">
          <svg class="contact__icon" viewBox="0 0 16 16" aria-hidden="true"><path d="M8 0.5a5.5 5.5 0 0 0-5.5 5.5c0 4 5.5 9.5 5.5 9.5s5.5-5.5 5.5-9.5A5.5 5.5 0 0 0 8 0.5z"/><circle cx="8" cy="6" r="2" fill="#fff"/></svg>
          <span>Jacaranda 415<br>Bahía Serena, Costa Azul CP 70420</span>
        </li>
      </ul>
    </div>
  </section>
</main>
</body>
</html>
```